Residential Remodeling Contractor needs updated business card

I need a new design for my business card.
Name of the company is Ridgefell Construction. I need a card that commands presence, strength, integrity. I have been in business for 28 years. I am a Residential Remodeling Contractor that covers all aspects of a residential remodel and build.

```html
<!DOCTYPE html>
<html lang="en">
<head>
<meta charset="utf-8">
<title>Ridgefell Construction – Business Card</title>
<link href="https://fonts.googleapis.com/css2?family=Noto+Serif:wght@700&family=Arimo:wght@400&display=swap" rel="stylesheet">
<style>
  :root {
    --navy: #17397a;
    --navy-deep: #1f3a7a;
    --ink: #333333;
    --paper: #ffffff;
    --backdrop: #9a9a9a;
  }
  * { margin: 0; padding: 0; box-sizing: border-box; }
  html, body { width: 1200px; height: 1059px; overflow: hidden; }
  body { background: var(--backdrop); position: relative; font-family: "Arimo", Arial, sans-serif; }

  .card {
    position: absolute;
    width: 688px;
    height: 390px;
    border-radius: 24px;
    overflow: hidden;
  }
  .card--front { left: 256px; top: 89px; background: var(--paper); }
  .card--back { left: 256px; top: 569px; }

  .name-marker { position: absolute; left: 0; top: 68px; width: 19px; height: 43px; background: var(--navy); }
  .holder-name {
    position: absolute; left: 35px; top: 60px;
    font-family: "Noto Serif", Georgia, serif; font-weight: 700;
    font-size: 27px; color: var(--navy); letter-spacing: 0.2px;
  }
  .holder-title { position: absolute; left: 35px; top: 92px; font-size: 17px; color: var(--ink); }

  .wordmark {
    position: absolute; right: 36px; top: 110px; text-align: right;
    font-family: "Noto Serif", Georgia, serif; font-weight: 700;
    text-transform: uppercase; color: var(--navy); line-height: 1.05;
  }
  .wordmark__line--top { font-size: 33px; letter-spacing: 1px; }
  .wordmark__line--bottom { font-size: 24px; letter-spacing: 0.5px; }

  .contact-list { position: absolute; left: 35px; top: 277px; list-style: none; }
  .contact-list li { display: flex; align-items: center; height: 27px; font-size: 17px; color: var(--ink); }
  .contact-list svg { width: 12px; height: 12px; margin-right: 7px; fill: var(--navy); flex: none; }

  .address { position: absolute; right: 36px; top: 306px; text-align: right; font-size: 17px; color: var(--ink); line-height: 25px; }

  .base-band { position: absolute; left: 443px; top: 379px; width: 209px; height: 11px; background: var(--navy); }

  .back-field {
    position: absolute; inset: 0;
    background: linear-gradient(100deg, #1d3672 0%, #233f80 45%, #4c6aac 80%, #7f9fd6 100%);
  }
  .wordmark--reverse {
    right: auto; left: 454px; top: 266px; text-align: left; color: var(--paper);
  }
  .wordmark--reverse .wordmark__line--top { font-size: 22px; }
  .wordmark--reverse .wordmark__line--bottom { font-size: 16px; }
</style>
</head>
<body>

  <section class="card card--front" aria-label="Business card front">
    <div class="name-marker"></div>
    <h1 class="holder-name">PETER CALLOWAY</h1>
    <p class="holder-title">Owner &amp; Manager</p>

    <div class="wordmark">
      <div class="wordmark__line--top">Ridgefell</div>
      <div class="wordmark__line--bottom">Construction</div>
    </div>

    <ul class="contact-list">
      <li>
        <svg viewBox="0 0 24 24"><path d="M2 8c0-3 4-5 10-5s10 2 10 5v2h-5V8c-1-1-3-1.5-5-1.5S8 7 7 8v2H2z"/><path d="M5 12h14l2 9H3z"/></svg>
        555 014 2287
      </li>
      <li>
        <svg viewBox="0 0 24 24"><path d="M2 10l10-7 10 7v11H2z" opacity=".35"/><path d="M2 10l10 7 10-7v11H2z"/></svg>
        info@ridgefellconstruction.com
      </li>
      <li>
        <svg viewBox="0 0 24 24"><circle cx="12" cy="12" r="10"/><path d="M7 6c3 1 2 4 5 4s1 4-2 5-3 4-3 4" stroke="#fff" stroke-width="2" fill="none"/></svg>
        www.ridgefellconstruction.com
      </li>
    </ul>

    <address class="address" style="font-style: normal;">
      P.O. Box&nbsp; Street Name<br>
      Country Name AB, A5B 521
    </address>

    <div class="base-band"></div>
  </section>

  <section class="card card--back" aria-label="Business card back">
    <div class="back-field" role="img" aria-label="Repeating pattern of the company mark in shades of navy fading to light blue"></div>
    <div class="wordmark wordmark--reverse">
      <div class="wordmark__line--top">Ridgefell</div>
      <div class="wordmark__line--bottom">Construction</div>
    </div>
  </section>

</body>
</html>
```